Business card for Sports Apparel business

DOUBLE SIDED DESIGN
We need business cards for a new sports apparel business. We are developing a protective headband for soccer initially.
Torvalle is focused on designing and developing head protection products to reduce the likelihood of concussion when playing sports. Exploring and understanding medical insights, material science research, current and former players experiences and governing bodies guidelines has allowed Torvalle to develop the safety, style, form and function requirements of a suitable product to bring to market.
Target Market(s)
Mums buying kits for the sons and daughters. Amateur footballers.
Industry/Entity Type
Sporting Good
Contact Information for Business Card
Martin Ashworth - CEO
Mobile: +44 7431589027
Email: martin@torvalle.co.uk
Tel: 0208 5519372
Helena Pargeter - COO
Mob: +44 7385 640117
Email: helena@torvalle.co.uk
Tel: 0208 5519372
Duncan Farrow - CCO
Mob: +44 7564 293081
Email: duncan@torvalle.co.uk
Tel: 0208 5519372
Look and feel
Each slider illustrates characteristics of the customer's brand and the style your logo design should communicate.

```html
<!DOCTYPE html>
<html lang="en">
<head>
<meta charset="utf-8">
<title>Torvalle – Business Card</title>
<link rel="stylesheet" href="https://fonts.googleapis.com/css2?family=Roboto:wght@400;500;700&display=swap">
<style>
  :root {
    --page-bg: #ededed;
    --card-bg: #fbfbfb;
    --blue-deep: #0b5fa3;
    --blue-mid: #1473b8;
    --blue-light: #2a86c9;
    --ink: #555a60;
    --ink-soft: #7a7f85;
    --rule: #8d9095;
    --texture-a: #f4f4f4;
    --texture-b: #e9e9e9;
  }
  * { box-sizing: border-box; margin: 0; padding: 0; }
  html, body { width: 1200px; height: 800px; overflow: hidden; }
  body {
    background: var(--page-bg);
    font-family: "Roboto", Arial, sans-serif;
    color: var(--ink);
    position: relative;
  }
  .card {
    position: absolute;
    left: 300px;
    width: 600px;
    height: 343px;
    background: var(--card-bg);
    overflow: hidden;
    box-shadow: 0 6px 18px rgba(0,0,0,0.12);
  }
  .card--back { top: 22px; }
  .card--front { top: 435px; }
  .card__texture {
    position: absolute; inset: 0;
    background: radial-gradient(circle at 40% 45%, var(--texture-b), var(--texture-a) 70%);
  }
  .card__shapes { position: absolute; inset: 0; width: 100%; height: 100%; }
  .brand {
    position: absolute;
    display: flex; align-items: center; gap: 10px;
    font-weight: 500;
    letter-spacing: 2px;
    color: var(--ink);
    text-transform: uppercase;
  }
  .brand__mark { background: var(--blue-deep); display: block; }
  .card--back .brand {
    left: 50%; top: 50%;
    transform: translate(-50%, -50%);
    font-size: 34px;
  }
  .card--back .brand__mark { width: 22px; height: 22px; }
  .card--front .brand { left: 38px; top: 42px; font-size: 28px; }
  .card--front .brand__mark { width: 18px; height: 18px; }
  .contact { position: absolute; left: 355px; top: 158px; }
  .contact__name {
    font-size: 18px; font-weight: 700; color: var(--blue-deep);
    text-transform: uppercase; letter-spacing: 0.3px;
  }
  .contact__role { font-size: 12px; color: var(--ink-soft); margin-top: 3px; }
  .contact__rule { width: 70px; height: 2px; background: var(--blue-deep); margin: 7px 0 12px; }
  .contact__list { list-style: none; }
  .contact__item {
    display: flex; align-items: center; gap: 10px;
    font-size: 15px; font-weight: 500; color: var(--ink);
    margin-bottom: 9px;
  }
  .contact__icon {
    width: 20px; height: 20px; border-radius: 50%;
    background: var(--blue-deep);
    display: flex; align-items: center; justify-content: center;
    flex: none;
  }
  .contact__icon svg { width: 12px; height: 12px; }
</style>
</head>
<body>

<section class="card card--back" aria-label="Card back">
  <div class="card__texture" role="img" aria-label="Faint grey hexagon texture"></div>
  <svg class="card__shapes" viewBox="0 0 600 343" aria-hidden="true">
    <polygon points="0,0 360,0 0,165" fill="var(--blue-mid)"/>
    <polygon points="0,0 250,0 0,115" fill="var(--blue-deep)"/>
    <polygon points="600,343 230,343 600,175" fill="var(--blue-mid)"/>
    <polygon points="600,343 360,343 600,235" fill="var(--blue-light)"/>
    <line x1="60" y1="155" x2="350" y2="22" stroke="var(--rule)" stroke-width="1"/>
    <line x1="150" y1="130" x2="310" y2="57" stroke="var(--rule)" stroke-width="1"/>
    <line x1="250" y1="322" x2="560" y2="180" stroke="var(--rule)" stroke-width="1"/>
    <line x1="300" y1="282" x2="470" y2="204" stroke="var(--rule)" stroke-width="1"/>
  </svg>
  <div class="brand"><span class="brand__mark"></span>Torvalle</div>
</section>

<section class="card card--front" aria-label="Card front">
  <div class="card__texture" role="img" aria-label="Faint grey hexagon texture"></div>
  <svg class="card__shapes" viewBox="0 0 600 343" aria-hidden="true">
    <polygon points="0,150 0,343 390,343" fill="var(--blue-mid)"/>
    <polygon points="0,235 0,343 250,343" fill="var(--blue-light)"/>
    <polygon points="600,0 600,150 470,0" fill="var(--blue-mid)"/>
    <polygon points="600,0 600,70 540,0" fill="var(--blue-deep)"/>
    <line x1="120" y1="215" x2="360" y2="330" stroke="var(--rule)" stroke-width="1"/>
    <line x1="280" y1="18" x2="470" y2="130" stroke="var(--rule)" stroke-width="1"/>
    <line x1="320" y1="20" x2="420" y2="80" stroke="var(--rule)" stroke-width="1"/>
  </svg>
  <div class="brand"><span class="brand__mark"></span>Torvalle</div>
  <div class="contact">
    <p class="contact__name">Martin Ashworth</p>
    <p class="contact__role">Chief Executive Officer</p>
    <div class="contact__rule"></div>
    <ul class="contact__list">
      <li class="contact__item">
        <span class="contact__icon"><svg viewBox="0 0 12 12"><rect x="3.5" y="1" width="5" height="10" rx="1" fill="none" stroke="#fff" stroke-width="1.2"/><circle cx="6" cy="9.3" r="0.6" fill="#fff"/></svg></span>
        +44 7431589027
      </li>
      <li class="contact__item">
        <span class="contact__icon"><svg viewBox="0 0 12 12"><rect x="1.5" y="3" width="9" height="6.5" fill="none" stroke="#fff" stroke-width="1.1"/><polyline points="1.5,3 6,7 10.5,3" fill="none" stroke="#fff" stroke-width="1.1"/></svg></span>
        martin@torvalle.co.uk
      </li>
      <li class="contact__item">
        <span class="contact__icon"><svg viewBox="0 0 12 12"><path d="M3 1.5 L4.8 3.6 L3.9 4.8 C4.5 6.2 5.8 7.5 7.2 8.1 L8.4 7.2 L10.5 9 L9.4 10.5 C5.5 10.2 1.8 6.5 1.5 2.6 Z" fill="#fff"/></svg></span>
        0208 5519372
      </li>
    </ul>
  </div>
</section>

</body>
</html>
```